New Business Card for Web Design/Internet Marketing Company

Looking for a great looking new business card. We are a 10 year old web design, internet marketing and website management company that works mostly with small businesses.

Our new card needs to better match the colors and style of our website, be bold, extremely usable and slightly edgy.

Target Market(s)

Small/Medium businesses that have websites

Industry/Entity Type

Internet

Requirements
Must have
• Front and back design, full color, rounded corners please

Must use the colors/style of our website (JPG provided)

INFO FOR CARDS (as readable as possible please)
Mark Lenner
President/CEO
mark@trelvanmedia.example
Phone: 520-381-7459
Toll Free: 866-381-7459
Address: 4315 W. Calloway Ave. Ste. 140, Tucson, AZ 85792

THINGS I WANT TO PROMOTE (if there is room):
1. Our Website - www.trelvanmedia.example

2. Social Media
Twitter: @trelvanmedia
Facebook: www.facebook.com/trelvanmedia

3. Our Services
Web Design
Internet Marketing
Website Management

```html
<!DOCTYPE html>
<html lang="en">
<head>
<meta charset="utf-8">
<title>Trelvan Media – Business Card</title>
<link href="https://fonts.googleapis.com/css2?family=Source+Sans+3:wght@400;600;700&display=swap" rel="stylesheet">
<style>
  :root {
    --stage: #ece9e4;
    --card-white: #ffffff;
    --brand-blue: #1b98d5;
    --brand-orange: #f5821f;
    --ink: #4a4a4a;
    --ink-soft: #6d6d6d;
    --rule: #c9c9c9;
    --decor: rgba(255,255,255,.08);
  }
  * { box-sizing: border-box; margin: 0; padding: 0; }
  html, body {
    width: 1200px; height: 422px; overflow: hidden;
    background: var(--stage);
    font-family: "Source Sans 3", "Helvetica Neue", Arial, sans-serif;
  }
  .canvas { position: relative; width: 1200px; height: 422px; }
  .card {
    position: absolute; top: 52px; width: 526px; height: 300px;
    border-radius: 18px; overflow: hidden;
    box-shadow: 0 2px 6px rgba(0,0,0,.18);
  }
  .card--front { left: 52px; background: var(--card-white); }
  .card--back { left: 611px; background: var(--brand-blue); color: #fff; }

  /* front */
  .brand { position: absolute; left: 24px; top: 132px; width: 236px; text-align: right; }
  .brand__line { display: flex; align-items: center; justify-content: flex-end; }
  .brand__mark {
    width: 20px; height: 20px; border-radius: 50%;
    background: var(--brand-orange); margin-right: 6px; flex: none;
  }
  .brand__name {
    font-size: 33px; font-weight: 700; color: var(--brand-blue);
    letter-spacing: -0.5px; line-height: 36px;
  }
  .brand__tagline { margin-top: 2px; font-size: 14px; color: var(--ink-soft); }
  .divider {
    position: absolute; left: 281px; top: 58px; width: 1px; height: 138px;
    background: var(--rule);
  }
  .contact { position: absolute; left: 302px; top: 68px; font-size: 14px; color: var(--ink); }
  .contact__line { display: flex; align-items: center; height: 19px; }
  .contact__line svg { width: 11px; height: 11px; margin-right: 7px; fill: var(--ink); flex: none; }
  .address { position: absolute; left: 304px; top: 157px; font-size: 14px; line-height: 19px; color: var(--ink); }
  .waves { position: absolute; left: 0; top: 0; }
  .holder {
    position: absolute; left: 40px; bottom: 14px; color: #fff;
    font-size: 17px; font-weight: 700;
  }
  .holder__title { font-size: 14px; font-weight: 400; }

  /* back */
  .back__decor {
    position: absolute; left: 100px; top: 40px; width: 300px; height: 250px;
    border-radius: 50%; background: var(--decor);
  }
  .services { position: absolute; left: 0; right: 0; top: 102px; text-align: center; }
  .services__title { font-size: 22px; font-weight: 700; margin-bottom: 12px; line-height: 30px; }
  .services__list { font-size: 21px; font-weight: 700; line-height: 28px; }
  .services__item::before { content: "•"; margin-right: 6px; }
  .services__item + .services__item { margin-left: 16px; }
  .social {
    position: absolute; left: 0; right: 0; top: 250px;
    display: flex; justify-content: center; gap: 16px; font-size: 18px;
  }
  .social__item { display: flex; align-items: center; }
  .social__item::before {
    content: ""; width: 13px; height: 13px; margin-right: 6px;
    background: rgba(255,255,255,.85); border-radius: 2px;
  }
</style>
</head>
<body>
<main class="canvas">
  <section class="card card--front">
    <svg class="waves" width="526" height="300" viewBox="0 0 526 300">
      <path d="M0 232 C120 222 250 226 370 250 C440 264 495 262 526 246 L526 254 C490 272 440 276 370 266 C250 248 120 244 0 252 Z" fill="var(--brand-orange)"/>
      <path d="M0 258 C130 248 260 256 380 276 C445 288 495 284 526 272 L526 300 L0 300 Z" fill="var(--brand-blue)"/>
    </svg>
    <div class="brand">
      <div class="brand__line"><span class="brand__mark"></span><span class="brand__name">trelvanmedia</span></div>
      <p class="brand__tagline">Grow your Presence</p>
    </div>
    <div class="divider"></div>
    <div class="contact">
      <p class="contact__line"><svg viewBox="0 0 12 12"><path d="M3 1 L5 3.5 L4 5 Q5 7 7 8 L8.5 7 L11 9 L10 11 Q4 11 1 2 Z"/></svg>866-381-7459</p>
      <p class="contact__line"><svg viewBox="0 0 12 12"><path d="M3 1 L5 3.5 L4 5 Q5 7 7 8 L8.5 7 L11 9 L10 11 Q4 11 1 2 Z"/></svg>520-381-7459</p>
      <p class="contact__line"><svg viewBox="0 0 12 12"><path d="M1 3 H11 V10 H1 Z M1 3 L6 7 L11 3" fill="none" stroke="#4a4a4a" stroke-width="1.4"/></svg>mark@trelvanmedia.example</p>
      <p class="contact__line"><svg viewBox="0 0 12 12"><circle cx="6" cy="6" r="5"/></svg>www.trelvanmedia.example</p>
    </div>
    <p class="address">4315 W. Calloway Ave. Ste. 140<br>Tucson, AZ 85792</p>
    <p class="holder">Mark Lenner , <span class="holder__title">President/CEO</span></p>
  </section>

  <section class="card card--back">
    <div class="back__decor" aria-hidden="true"></div>
    <div class="services">
      <h2 class="services__title">Our Services</h2>
      <div class="services__list">
        <span class="services__item">Web Design</span><span class="services__item">Internet Marketing</span><br>
        <span class="services__item">Website Management</span>
      </div>
    </div>
    <div class="social">
      <span class="social__item">@trelvanmedia</span>
      <span class="social__item">trelvanmedia</span>
    </div>
  </section>
</main>
</body>
</html>
```